I am a home builder and developer

I would like some sort of architectural design like a pencil type of drawing of a house but want it to be professional looking and two sided.

Simply I am a custom home builder and land developer. I would like a new design other than what I have now that's what I thought y'all did. I like mostly black maybe with an pencil type of drawing of a house. Like an architectural look.

Industry/Entity Type

Home Builder

```html
<!DOCTYPE html>
<html lang="en">
<head>
<meta charset="utf-8">
<title>Halvern Building Inc – Business Card</title>
<link rel="stylesheet" href="https://fonts.googleapis.com/css2?family=Open+Sans:wght@400;700&family=Questrial&family=Noto+Serif:wght@400&display=swap">
<style>
  :root {
    --backdrop: #dcdadb;
    --card-dark: #1a1a1b;
    --card-light: #f1f1f1;
    --accent-red: #b3202f;
    --ink-dark: #3c3c3e;
    --ink-mid: #707072;
    --ink-light: #f4f4f4;
  }
  * { margin: 0; padding: 0; box-sizing: border-box; }
  html, body {
    width: 1200px; height: 900px; overflow: hidden;
    background: var(--backdrop);
    font-family: "Open Sans", sans-serif;
  }
  .stage { position: relative; width: 1200px; height: 900px; }
  .card {
    position: absolute; left: 320px;
    width: 560px; height: 320px;
    border-radius: 22px;
    box-shadow: 0 6px 14px rgba(0,0,0,.18);
    overflow: hidden;
  }
  .card--front { top: 80px; background: var(--card-dark); }
  .card--back  { top: 480px; background: var(--card-light); }

  .brand {
    display: flex; align-items: center; gap: 10px;
    font-weight: 700; letter-spacing: 2px; text-transform: uppercase;
  }
  .brand__square { flex: none; width: 12px; height: 12px; background: var(--accent-red); }
  .card--front .brand {
    position: absolute; top: 118px; left: 0; right: 0; justify-content: center;
    color: var(--ink-light); font-size: 24px;
  }
  .tagline {
    position: absolute; top: 186px; left: 0; right: 0; text-align: center;
    color: var(--ink-light); font-size: 15px;
  }

  .card--back .brand {
    position: absolute; top: 134px; left: 40px; width: 220px;
    color: var(--ink-dark); font-size: 17px; line-height: 1.3;
  }
  .card--back .brand__name { max-width: 180px; }
  .divider {
    position: absolute; left: 290px; top: 44px; width: 1px; height: 176px;
    background: var(--ink-dark);
  }
  .contact { position: absolute; left: 316px; top: 48px; }
  .contact__name {
    font-family: "Questrial", sans-serif; font-size: 28px; color: var(--ink-dark);
    line-height: 1.1;
  }
  .contact__title {
    font-family: "Noto Serif", serif; font-size: 17px; color: var(--accent-red);
    margin-bottom: 14px;
  }
  .contact__row {
    display: flex; align-items: center; gap: 10px;
    font-size: 14px; color: var(--ink-mid); margin-bottom: 6px;
  }
  .contact__row svg { width: 16px; height: 16px; fill: var(--accent-red); }
  .licenses {
    position: absolute; right: 30px; bottom: 30px;
    font-size: 14px; color: var(--ink-mid);
  }
  .licenses__label { color: var(--accent-red); }
</style>
</head>
<body>
<div class="stage">
  <section class="card card--front">
    <div class="brand"><span class="brand__square"></span><span class="brand__name">Halvern Building Inc</span></div>
    <p class="tagline">Custom home builder and land developer</p>
  </section>

  <section class="card card--back">
    <div class="brand"><span class="brand__square"></span><span class="brand__name">Halvern Building Inc</span></div>
    <div class="divider"></div>
    <div class="contact">
      <p class="contact__name">Jonah Pell</p>
      <p class="contact__title">President and Owner</p>
      <p class="contact__row">
        <svg viewBox="0 0 16 16" aria-hidden="true"><path d="M2 5c0-2 2-3 6-3s6 1 6 3v1h-3V4.5H5V6H2zM4 7h8l2 6H2zM8 8.5a2 2 0 1 0 0 4 2 2 0 0 0 0-4z"/></svg>
        555-014-2287
      </p>
      <p class="contact__row">
        <svg viewBox="0 0 16 16" aria-hidden="true"><path d="M1 3h14v10H1zM2 4.2v.6l6 4 6-4v-.6z" fill-rule="evenodd"/></svg>
        office@halvernbuild.com
      </p>
    </div>
    <p class="licenses"><span class="licenses__label">Licenses :</span> VA 0000481123 | NC 40318</p>
  </section>
</div>
</body>
</html>
```